Novexa company website, a website for employment for people with autism

The website will make a match between people and jobs, mainly in the graphical sector, but also other sectors.
The name of the company is novexa and automates jobs with people that are on the autism spectrum.
The whole matchmaking and feedback process and so doesn't have to be in this prototype, we just want the general information pages and to convey a great look and brand identity that we will keep in the other pages to be developed. The website must be made with Wordpress, since the backend will be developed in Wordpress too.
It is a social project that wants to create possibilites for people with ASS to work from home for an employer or to do a variety of tasks for different customers.
The people we hire are generally not on the regular job market or have difficulty finding a job and "selling themselves"

Target Market(s)

matchmaking between talent (with ASS) and employers / jobs

Number of Pages Required

5+ page

Font styles to use
Sans Serif

Colors
ec1f27
e34298
a64599
6b449b
0355a3
0792cd

Requirements
Must have
• A stunning landing pages
• Integrate our logo and must match with what will do. We want a clean, modern, minimalistic, sleek website that radiates creativity and good looks.
• We have one page describing what we can do for customers, one page for people with ASS that would like to be candidates (our approach, learning program, ...), two pages that are addressed to partners who want to cooperate: the one's that can assist with autism related assistance and the one's that can help with the job coaching.
Nice to have
• In our logo are many colors as we embrace diversity and want to show that. Out main branding colors are red (for action) and blue for stability and will all gradients that go with it. Mainly white or black (or anthracite) for other parts
Should not have
• We want a modern and minimalistic design, no fluffy designs with lots of ornaments.

```html
<!DOCTYPE html>
<html lang="en">
<head>
<meta charset="utf-8">
<title>Novexa</title>
<link href="https://fonts.googleapis.com/css2?family=Montserrat:wght@400;500;600;700&family=Barlow:ital,wght@0,400;0,500;0,600;1,400&display=swap" rel="stylesheet">
<style>
:root{
  --red:#ec1f27;--pink:#e34298;--purple:#a64599;--violet:#6b449b;--blue:#0355a3;--sky:#0792cd;
  --ink:#222;--text:#444;--grey:#ebebeb;--stripe:#f3f3f3;--white:#fff;
}
*{margin:0;padding:0;box-sizing:border-box}
html,body{width:1200px;height:4000px;overflow:hidden;background:var(--white)}
body{position:relative;font-family:'Barlow',sans-serif;color:var(--text)}
.abs{position:absolute}
h1,h2,h3,h4,.brand,.nav a,.btn{font-family:'Montserrat',sans-serif}
.brand{font-weight:700;font-size:44px;letter-spacing:6px;color:var(--ink);display:flex;align-items:center;gap:14px}
.brand .dot{width:26px;height:26px;border-radius:50%;background:var(--pink)}
.call{right:112px;top:22px;font-family:'Montserrat',sans-serif;font-weight:700;font-size:22px;color:var(--ink);display:flex;align-items:center;gap:8px}
.call span{color:var(--red)}
.nav{right:112px;top:74px;display:flex;gap:42px}
.nav a{text-decoration:none;color:var(--ink);font-weight:600;font-size:15px}
.hero{left:0;top:117px;width:1200px;height:590px;background:linear-gradient(100deg,#3a2746 0%,#e34298 30%,#b5479e 50%,#3f7de0 72%,#1b2f8c 100%)}
.hero-word{left:0;top:455px;width:1200px;text-align:center;font-family:'Montserrat',sans-serif;font-weight:700;font-size:110px;letter-spacing:16px;color:rgba(255,255,255,.22)}
.play{left:563px;top:384px;width:74px;height:74px;border-radius:50%;background:var(--white);display:flex;align-items:center;justify-content:center}
.stripe{background:var(--stripe)}
.photo{border-radius:50%}
h2.title{font-weight:500;font-size:40px;color:var(--ink);letter-spacing:1px}
.center{left:0;width:1200px;text-align:center}
p.lead{font-size:15px;line-height:26px;color:var(--text)}
.about p.lead{font-size:14px}
.btn{display:flex;align-items:center;justify-content:center;background:var(--blue);color:var(--white);font-weight:600;font-size:14px;border-radius:22px;height:43px}
.card-img{width:424px;height:296px}
.card-box{width:430px;height:261px;background:var(--grey);padding:0 36px}
.card-box h3{margin-top:152px;font-weight:600;font-size:20px;color:var(--ink)}
.card-box p{margin-top:12px;font-size:14px;line-height:24px}
.feature{width:200px}
.feature h4{margin-top:0;font-weight:600;font-size:19px;color:var(--ink)}
.feature .bar{width:70px;height:4px;margin:12px 0 18px}
.feature p{font-size:15px;line-height:27px}
.news{left:112px;top:3299px;width:976px;height:250px;border-radius:18px;background:linear-gradient(100deg,var(--red) 0%,#c21f4a 35%,var(--violet) 70%,var(--blue) 100%);overflow:hidden}
.news h2{position:absolute;left:247px;top:40px;font-weight:500;font-size:40px;color:var(--white)}
.news .sub{position:absolute;left:247px;top:96px;font-style:italic;font-size:16px;color:var(--white)}
.news-art{position:absolute;left:28px;top:26px;width:190px;height:198px;border-radius:10px;background:rgba(255,255,255,.28)}
.field{position:absolute;left:245px;top:138px;width:550px;height:54px;background:var(--white);border-radius:27px 0 0 27px;padding-left:28px;display:flex;align-items:center;font-size:16px;color:var(--ink)}
.sign{position:absolute;left:795px;top:138px;width:120px;height:54px;background:var(--red);border-radius:0 27px 27px 0;color:var(--white);font-family:'Montserrat',sans-serif;font-weight:600;font-size:17px;display:flex;align-items:center;justify-content:center}
.social{display:flex;gap:8px;left:952px;top:3602px}
.social i{width:27px;height:27px;border-radius:50%;display:block}
.rule{height:1px;background:#ddd}
.fhead{font-family:'Montserrat',sans-serif;font-weight:500;font-size:17px;color:var(--ink)}
.flist{list-style:none;font-size:14px;line-height:21.5px;color:var(--text)}
.contact-row{display:flex;gap:18px;align-items:flex-start;font-size:14px;line-height:21px}
.copy{font-size:14px;color:var(--ink)}
</style>
</head>
<body>

<header>
  <div class="abs brand" style="left:112px;top:36px"><i class="dot"></i>NOVEXA</div>
  <div class="abs call">
    <svg width="20" height="20" viewBox="0 0 24 24"><path fill="#ec1f27" d="M6.6 10.8a15.1 15.1 0 0 0 6.6 6.6l2.2-2.2c.3-.3.7-.4 1-.2 1.1.4 2.3.6 3.6.6.6 0 1 .4 1 1V20c0 .6-.4 1-1 1A17 17 0 0 1 3 4c0-.6.4-1 1-1h3.5c.6 0 1 .4 1 1 0 1.3.2 2.5.6 3.6.1.3 0 .7-.2 1z"/></svg>
    CALL US:<span>555.204.7731</span>
  </div>
  <nav class="abs nav"><a>HOME</a><a>ABOUT</a><a>SERVICES</a><a>PROJECTS</a><a>NEWS</a><a>CONTACT</a></nav>
</header>

<section class="abs hero" role="img" aria-label="Pink and blue coloured smoke cloud video still"></section>
<div class="abs hero-word">NOVEXA</div>
<div class="abs play"><svg width="28" height="30" viewBox="0 0 28 30"><path d="M4 2l22 13L4 28z" fill="#ec1f27"/></svg></div>

<section class="about">
  <div class="abs stripe" style="left:0;top:710px;width:75px;height:405px"></div>
  <div class="abs stripe" style="left:96px;top:710px;width:36px;height:470px"></div>
  <div class="abs stripe" style="left:160px;top:710px;width:36px;height:420px"></div>
  <div class="abs photo" style="left:115px;top:968px;width:224px;height:224px;background:linear-gradient(150deg,var(--red),var(--pink) 50%,var(--blue))"></div>
  <div class="abs photo" role="img" aria-label="Young man working at a workbench" style="left:248px;top:792px;width:374px;height:374px;background:linear-gradient(135deg,#4a4238,#8a2a2e 55%,#2e2a28)"></div>
  <div class="abs photo" role="img" aria-label="Smiling young woman at a table" style="left:227px;top:1075px;width:266px;height:266px;background:linear-gradient(160deg,#b9ab93,#e8e2d8 55%,#8f8576);border:6px solid #fff"></div>
  <h2 class="abs title" style="left:677px;top:872px">ABOUT US</h2>
  <p class="abs lead" style="left:677px;top:936px;width:400px">Sed ut perspiciatis unde omnis iste natus error sitvoluptatem accusantium doloremque laudantium, totamque ipsa quae ab illo inventore veritatis et quasi architecto beatae vitae dic ta sunt explicabomo enimtatemed ut perspiciatis unde omnis iste natus error sitvoluptatem accusantium doloremque laud antium, totamque ipsa quae ab illo inventore veritatis et qu asi architecto beatae vitae dic ta sunt explicabomo</p>
  <div class="abs btn" style="left:677px;top:1141px;width:132px">READ MORE</div>
</section>

<section class="projects">
  <h2 class="abs title center" style="top:1450px">PROJECTS</h2>
  <p class="abs lead center" style="top:1510px;padding:0 235px">Sed ut perspiciatis unde omnis iste natus error sit voluptatem accusantium doloremque laudantium, totamque ipsa quae ab illo inventore veritatis et quasi architecto beatae vitae dicta sunt explicabomo enimtatem.</p>

  <div class="abs card-box" style="left:149px;top:1792px"><h3>Project Name</h3><p>Sed ut perspiciatis unde omnis iste nat sit voluptatem accusantium doloremque laudantium, totamaa.</p></div>
  <div class="abs card-img" role="img" aria-label="Young women baking together in a kitchen" style="left:112px;top:1616px;background:linear-gradient(135deg,#cfd6dc,#9aa7b1 50%,#d9c9b8)"></div>

  <div class="abs card-box" style="left:658px;top:1792px"><h3>Project Name</h3><p>Sed ut perspiciatis unde omnis iste nat sit voluptatem accusantium doloremque laudantium, totamaa.</p></div>
  <div class="abs card-img" role="img" aria-label="Two people laughing at a table, pink tinted" style="left:621px;top:1616px;background:linear-gradient(135deg,#6b449b,#a64599 50%,#e34298)"></div>

  <div class="abs card-box" style="left:149px;top:2264px"><h3>Project Name</h3><p>Sed ut perspiciatis unde omnis iste nat sit voluptatem accusantium doloremque laudantium, totamaa.</p></div>
  <div class="abs card-img" role="img" aria-label="Man in a suit working on a laptop, blue tinted" style="left:112px;top:2088px;background:linear-gradient(135deg,#0a2f5c,#0355a3 55%,#1b6fa8)"></div>

  <div class="abs card-box" style="left:658px;top:2264px"><h3>Project Name</h3><p>Sed ut perspiciatis unde omnis iste nat sit voluptatem accusantium doloremque laudantium, totamaa.</p></div>
  <div class="abs card-img" role="img" aria-label="Two smiling friends outdoors" style="left:621px;top:2088px;background:linear-gradient(135deg,#c8c2a8,#e6dc8a 50%,#8c7f62)"></div>

  <div class="abs btn" style="left:533px;top:2570px;width:134px">VIEW ALL</div>
</section>

<section class="why">
  <h2 class="abs title center" style="top:2714px">WHY CHOOSE NOVEXA</h2>
  <p class="abs lead center" style="top:2784px;padding:0 240px">Sed ut perspiciatis unde omnis iste natus error sit voluptatem accusantium doloremque laudantium, totamque ipsa quae ab illo inventore veritatis et quasi architecto beatae vitae dicta sunt explicabomo enimtatem.</p>

  <svg class="abs" style="left:112px;top:2885px" width="60" height="70" viewBox="0 0 60 70" fill="none" stroke="#0355a3" stroke-width="3"><circle cx="30" cy="28" r="16"/><path d="M23 48h14M24 55h12M27 62h6"/><path d="M30 4v-4M8 28H2M58 28h-6M13 11 9 7M47 11l4-4" stroke="#0792cd"/></svg>
  <div class="abs feature" style="left:112px;top:2985px"><h4>Suptacusantium</h4><div class="bar" style="background:var(--blue)"></div><p>Sed ut perspiciatis unde omnis iste natuserror sit voluptlortm accusantium dolorlaloru daloiu mtotam rem aperiam, eaquesa quae ab illo inventor.</p></div>

  <svg class="abs" style="left:371px;top:2885px" width="60" height="70" viewBox="0 0 60 70" fill="none" stroke="#ec1f27" stroke-width="3"><path d="M16 64V50C8 45 4 38 4 29 4 14 16 4 30 4s26 10 26 24c0 5-3 8-3 8l4 8-6 2v8c0 4-3 6-7 6h-6v6"/><circle cx="30" cy="27" r="9"/></svg>
  <div class="abs feature" style="left:371px;top:2985px"><h4>Suptacusantium</h4><div class="bar" style="background:var(--red)"></div><p>Sed ut perspiciatis unde omnis iste natuserror sit voluptlortm accusantium dolorlaloru daloiu mtotam rem aperiam, eaquesa quae ab illo inventor.</p></div>

  <svg class="abs" style="left:629px;top:2885px" width="70" height="70" viewBox="0 0 70 70" fill="none" stroke="#6b449b" stroke-width="3"><circle cx="32" cy="38" r="28"/><circle cx="32" cy="38" r="17"/><circle cx="32" cy="38" r="6"/><path d="M32 38 62 8M54 6v10h10" stroke="#a64599"/></svg>
  <div class="abs feature" style="left:629px;top:2985px"><h4>Suptacusantium</h4><div class="bar" style="background:var(--violet)"></div><p>Sed ut perspiciatis unde omnis iste natuserror sit voluptlortm accusantium dolorlaloru daloiu mtotam rem aperiam, eaquesa quae ab illo inventor.</p></div>

  <svg class="abs" style="left:888px;top:2885px" width="70" height="70" viewBox="0 0 70 70" fill="none" stroke="#e34298" stroke-width="3"><rect x="24" y="6" width="42" height="30" rx="3"/><path d="M24 8l21 16 21-16"/><path d="M8 34c-4 4-4 10 2 18s12 12 18 12c4 0 6-3 6-5l-7-6-4 3c-4-2-8-6-9-10l3-4-5-8z" stroke="#ec1f27"/></svg>
  <div class="abs feature" style="left:888px;top:2985px"><h4>Suptacusantium</h4><div class="bar" style="background:var(--pink)"></div><p>Sed ut perspiciatis unde omnis iste natuserror sit voluptlortm accusantium dolorlaloru daloiu mtotam rem aperiam, eaquesa quae ab illo inventor.</p></div>
</section>

<section class="abs news">
  <div class="news-art" role="img" aria-label="Decorative newsletter illustration"></div>
  <h2>Sign up to our newsletter</h2>
  <p class="sub">Neque porro quisquam est qui dolorem ipsum quia dolor sit amet, consectetu</p>
  <div class="field">Email:</div>
  <div class="sign">SIGN UP</div>
</section>

<footer>
  <div class="abs stripe" style="left:0;top:3600px;width:75px;height:400px"></div>
  <div class="abs stripe" style="left:96px;top:3690px;width:36px;height:310px"></div>
  <div class="abs stripe" style="left:160px;top:3690px;width:36px;height:310px"></div>
  <div class="abs stripe" style="left:290px;top:3780px;width:70px;height:220px"></div>
  <div class="abs brand" style="left:109px;top:3592px;font-size:34px;letter-spacing:5px"><i class="dot" style="width:20px;height:20px"></i>NOVEXA</div>
  <div class="abs social"><i style="background:var(--blue)"></i><i style="background:var(--sky)"></i><i style="background:var(--blue)"></i><i style="background:var(--red)"></i></div>
  <div class="abs rule" style="left:109px;top:3667px;width:982px"></div>

  <div class="abs fhead" style="left:109px;top:3690px">Contact</div>
  <div class="abs contact-row" style="left:109px;top:3726px">
    <svg width="24" height="30" viewBox="0 0 24 30" fill="none" stroke="#ec1f27" stroke-width="2"><path d="M12 29S2 17 2 11a10 10 0 0 1 20 0c0 6-10 18-10 18z"/><circle cx="12" cy="11" r="4"/></svg>
    <span>120 Harbor Lane,<br>Westfield, 40217</span></div>
  <div class="abs contact-row" style="left:109px;top:3792px">
    <svg width="24" height="24" viewBox="0 0 24 24" fill="none" stroke="#0355a3" stroke-width="2"><path d="M6.6 10.8a15 15 0 0 0 6.6 6.6l2.2-2.2 5.6 1.8V21A18 18 0 0 1 3 3h4.2l1.6 5.6z"/></svg>
    <span>5 550 123 456 78<br>5 550 987 654 32</span></div>
  <div class="abs contact-row" style="left:109px;top:3852px">
    <svg width="26" height="20" viewBox="0 0 26 20" fill="none" stroke="#ec1f27" stroke-width="2"><rect x="1" y="1" width="24" height="18"/><path d="M1 1l12 10L25 1"/></svg>
    <span>hello@novexa-mail.org<br>team@novexa-mail.org</span></div>

  <div class="abs fhead" style="left:413px;top:3690px">Projects</div>
  <ul class="abs flist" style="left:413px;top:3728px"><li>Lorem ipsum dolo</li><li>Consectetur adipiscing elit.</li><li>Fusce eget leo tincid</li><li>Donec consequat</li><li>Praesent elementum</li><li>Jmauris posuerel</li><li>Aenean a ex eu lectu</li></ul>
  <ul class="abs flist" style="left:661px;top:3728px"><li>Lorem ipsum dolo</li><li>Consectetur adipiscing elit.</li><li>Fusce eget leo tincid</li><li>Donec consequat</li><li>Praesent elementum</li><li>Jmauris posuerel</li><li>Aenean a ex eu lectu</li></ul>

  <div class="abs fhead" style="left:923px;top:3690px">Other Links</div>
  <ul class="abs flist" style="left:923px;top:3728px"><li>Lorem ipsum dolo</li><li>Consectetur adipiscing elit.</li><li>Fusce eget leo tincid</li><li>Donec consequat</li><li>Praesent elementum</li><li>Jmauris posuerel</li><li>Aenean a ex eu lectu</li></ul>

  <div class="abs rule" style="left:109px;top:3920px;width:982px"></div>
  <p class="abs copy center" style="top:3950px">Copyright 2019 All Rights Reserved</p>
</footer>

</body>
</html>
```